Health Care Company with Logo Needs Business Cards designed

We are a luxury behavioral health company looking for business cards design we already have a logo and are looking for someone to design a sophisticated luxurious looking business card. Please note that Card design should be captivating just like the logo and also encompass the logo color

Industry/Entity Type

Healthcare

Contact Information for Business Card

Logo,company name, tagline, my name and title, contact details, and physical address

```html
<!DOCTYPE html>
<html lang="en">
<head>
<meta charset="utf-8">
<title>Lumen Behavioral Health – Business Card</title>
<link href="https://fonts.googleapis.com/css2?family=Roboto+Condensed:wght@700&family=Oswald:wght@400&family=Roboto:wght@400&display=swap" rel="stylesheet">
<style>
  :root {
    --bg: #9a9a9a;
    --purple: #7f3f98;
    --blue: #00aeef;
    --blue-mid: #1e8fd8;
    --sky: #6ccbf0;
    --white: #ffffff;
    --rule: rgba(255,255,255,0.55);
  }
  * { margin: 0; padding: 0; box-sizing: border-box; }
  html, body { width: 1200px; height: 1200px; overflow: hidden; }
  body { background: var(--bg); position: relative; }

  .card { position: absolute; top: 303px; width: 368px; height: 594px; overflow: hidden; }

  /* Front */
  .card-front { left: 201px;
    background: linear-gradient(215deg, var(--sky) 0%, var(--blue-mid) 28%, #5a5fb4 55%, var(--purple) 80%, #7449a3 100%); }
  .front-art { position: absolute; inset: 0; }
  .front-brand { position: absolute; left: 32px; top: 497px; width: 306px; color: var(--white); }
  .front-brand .company { font: 700 30px/1 "Roboto Condensed", sans-serif; white-space: nowrap; }
  .front-brand .tagline { margin-top: 9px; font: 700 10.5px/1 "Roboto Condensed", sans-serif; letter-spacing: 3.2px; white-space: nowrap; }

  /* Back */
  .card-back { left: 599px; background: var(--purple); }
  .back-top { position: absolute; left: 0; top: 0; width: 100%; height: 292px; background: var(--white); border-bottom: 5px solid var(--blue); }
  .brand-dot { position: absolute; left: 162px; top: 108px; width: 44px; height: 44px; border-radius: 50%; background: var(--purple); }
  .back-brand { position: absolute; left: 0; top: 180px; width: 100%; text-align: center; }
  .back-brand .company { font: 700 30px/1 "Roboto Condensed", sans-serif; color: var(--purple); white-space: nowrap; }
  .back-brand .tagline { margin-top: 9px; font: 700 10.5px/1 "Roboto Condensed", sans-serif; letter-spacing: 3.2px; color: var(--blue); white-space: nowrap; }

  .person { position: absolute; left: 0; top: 322px; width: 100%; text-align: center; }
  .person .name { font: 400 40px/1 "Oswald", sans-serif; color: var(--blue); letter-spacing: -0.5px; }
  .person .title { margin-top: 4px; font: 400 17px/1 "Roboto", sans-serif; color: var(--white); letter-spacing: 0.3px; }

  .icon-row { position: absolute; left: 0; top: 395px; width: 100%; display: flex; justify-content: center; align-items: center; gap: 4px; }
  .icon-row .line { width: 52px; height: 1px; background: var(--rule); margin: 0 4px; }
  .icon { width: 25px; height: 25px; background: var(--blue); border-radius: 3px; display: flex; align-items: center; justify-content: center; }

  .contact { position: absolute; left: 0; top: 429px; width: 100%; text-align: center; font: 400 17px/22px "Roboto", sans-serif; color: var(--white); }
  .divider { position: absolute; left: 88px; top: 506px; width: 195px; height: 1px; background: var(--rule); }
  .address { position: absolute; left: 0; top: 520px; width: 100%; text-align: center; font: 400 17px/22px "Roboto", sans-serif; color: var(--white); }
</style>
</head>
<body>

<section class="card card-front">
  <div class="front-art" role="img" aria-label="Large soft brand symbol decoration over the gradient"></div>
  <div class="front-brand">
    <div class="company">Lumen Behavioral Health</div>
    <div class="tagline">COMMITTED TO CALM, CARE AND WELLBEING</div>
  </div>
</section>

<section class="card card-back">
  <div class="back-top">
    <div class="brand-dot"></div>
    <div class="back-brand">
      <div class="company">Lumen Behavioral Health</div>
      <div class="tagline">COMMITTED TO CALM, CARE AND WELLBEING</div>
    </div>
  </div>

  <div class="person">
    <div class="name">Daniel Hartley</div>
    <div class="title">MANAGING DIRECTOR</div>
  </div>

  <div class="icon-row">
    <span class="line"></span>
    <span class="icon">
      <svg width="15" height="15" viewBox="0 0 24 24" fill="none" stroke="#fff" stroke-width="2"><path d="M4 9c0-3 3-5 8-5s8 2 8 5v1h-4V8H8v2H4z" fill="#fff"/><rect x="6" y="12" width="12" height="8" rx="1"/><circle cx="12" cy="16" r="1.6" fill="#fff"/></svg>
    </span>
    <span class="icon">
      <svg width="16" height="13" viewBox="0 0 24 18" fill="none" stroke="#fff" stroke-width="2"><rect x="1" y="1" width="22" height="16"/><path d="M1 1l11 9 11-9M1 17l8-7M23 17l-8-7"/></svg>
    </span>
    <span class="icon">
      <svg width="16" height="16" viewBox="0 0 24 24" fill="none" stroke="#fff" stroke-width="2"><circle cx="12" cy="12" r="10"/><path d="M2 12h20M12 2c3 3 3 17 0 20M12 2c-3 3-3 17 0 20"/></svg>
    </span>
    <span class="line"></span>
  </div>

  <div class="contact">
    <div>044-555 210 347</div>
    <div>hello@lumenbh.com</div>
    <div>www.lumenbh.com</div>
  </div>

  <div class="divider"></div>

  <div class="address">
    <div>421, Address line goes here</div>
    <div>45452,Country Name</div>
  </div>
</section>

</body>
</html>
```